Redesign Digital Lending Mobile App - Android/ Flutter

Want to re-theme an existing Digital Lending Mobile app to simplify customer journeys, as well as uplift the UI.

Most users will have small screen phones so the design needs to take that into consideration while also adapting to those with larger devices, like admins with Tablets.

Have already laid out customer journeys on Figma with guidance on how the flow of the app should be. https://www.plankora.example/board/q4ZtRm81KdWe7YhXcvBnaL/LoomKit?frame-id=3-5182&s=Jk2pQwEr7TyUi-9

Video capture of current app: https://vaultbin.example/clip/7Hx3LmQp9RtZw2KcVn4YsBd8EfGj1/play
https://vaultbin.example/clip/4PsWq8ZnTk2LrXy6MbJc3VhGd9FeA/play

The documented views for Web are also here https://docshelf.example/open?ref=3B8F2204AD7C91E5!tk8d1f6a2c4e7b90d3f5a1c8e2b6d4f9a07&cid=3b8f2204ad7c91e5&kind=file%2Cdocx&wdo=2

Target Market(s)

Kenya, Tanzania, Uganda - Africa

Industry/Entity Type

Fintech

Requirements
Must have
• Responsive for diff screens, esp. in context of smaller screen smartphone
Nice to have
• Thematic components to ensure new views can easily be adapted to these themse

```html
<!DOCTYPE html>
<html lang="en">
<head>
<meta charset="utf-8">
<title>LoomKit — Lending App Screens</title>
<link rel="stylesheet" href="https://fonts.googleapis.com/css2?family=Lato:wght@400;700;900&display=swap">
<style>
:root{
  --canvas:#d9d9d9;
  --screen:#f5f7fc;
  --white:#ffffff;
  --blue:#3577c8;
  --blue-dark:#2d64ad;
  --green:#4a9e68;
  --track:#dbe4f7;
  --ink:#1e2230;
  --muted:#b3bccb;
  --line:#e3e7ef;
  --row-alt:#f7f8fb;
  --pill:#dde9f8;
}
*{box-sizing:border-box;margin:0;padding:0}
html,body{width:1200px;height:781px;overflow:hidden;background:var(--canvas)}
body{font-family:'Lato',sans-serif;color:var(--ink)}
.stage{position:absolute;left:0;top:0;width:1536px;height:1000px;transform:scale(.78125);transform-origin:0 0}
.screen{position:absolute;top:78px;width:390px;height:844px;background:var(--screen);border-radius:46px;overflow:hidden;box-shadow:0 2px 10px rgba(0,0,0,.05)}
.divider{position:absolute;height:1px;background:var(--line)}
.round-icon{position:absolute;width:38px;height:38px;border:2.5px solid var(--blue);border-radius:50%;display:flex;align-items:center;justify-content:center;background:var(--white)}
.round-icon svg{width:20px;height:20px}
.brand{position:absolute;left:20px;top:66px;font-weight:900;font-size:20px;color:var(--blue);letter-spacing:.3px}
.stat{position:absolute;top:137px;width:80px;height:46px;background:var(--blue);border-radius:7px;color:var(--white);font-size:10px;line-height:18px;padding:5px 0 0 9px}
.section-title{position:absolute;font-size:16px}
.chip{position:absolute;height:35px;background:var(--green);border-radius:6px;color:var(--white);font-size:12px;font-weight:700;display:flex;align-items:center;justify-content:center;gap:6px}
.chip::after{content:"";border:3.5px solid transparent;border-top:4px solid var(--white);margin-top:4px}
.metric-label,.metric-value{position:absolute;font-size:14px;transform:translateY(-50%)}
.metric-value{right:20px}
.track{position:absolute;left:21px;width:352px;height:8px;border-radius:4px;background:var(--track);overflow:hidden}
.track span{display:block;width:122px;height:100%;background:var(--blue);border-radius:4px}
.bar{position:absolute;background:var(--blue)}
.bar.up{background:var(--green)}
.axis{position:absolute;height:1px;background:#c9ced8}
.tick{position:absolute;font-size:8px;color:#444;transform:translateX(-50%)}
.btn-grad{position:absolute;border-radius:22px;color:var(--white);display:flex;align-items:center;justify-content:center;background:linear-gradient(90deg,var(--blue),var(--green));box-shadow:0 4px 6px rgba(0,0,0,.18)}
.nav{position:absolute;left:0;right:0;top:754px;height:90px;background:var(--white);border-top:1px solid var(--line)}
.nav-item{position:absolute;top:20px;width:70px;margin-left:-35px;text-align:center;color:var(--muted);font-size:13px}
.nav-item svg{display:block;margin:0 auto 6px;width:26px;height:26px;color:var(--muted)}
.nav-item.active{color:var(--green);font-weight:700}
.nav-item.active svg{color:var(--green)}
.nav-item.active.blue{color:var(--blue-dark)}
.title{position:absolute;font-size:22px;font-weight:900;transform:translateY(-50%)}
.summary-table{position:absolute;left:18px;top:130px;width:352px;border-collapse:collapse;background:var(--white);font-size:15px;letter-spacing:.2px}
.summary-table td{height:57.5px;padding:0 17px}
.summary-table td+td{border-left:1px solid var(--line);padding-left:25px;width:128px}
.summary-table tr:nth-child(even){background:var(--row-alt)}
.total{position:absolute;left:0;right:0;top:136px;text-align:center;font-size:26px;font-weight:900;color:var(--blue);transform:translateY(-50%)}
.toggle{position:absolute;top:242px;height:42px;border-radius:21px;display:flex;align-items:center;justify-content:center;font-size:19px}
.toggle.off{background:var(--pill);color:var(--blue)}
.week{position:absolute;top:330px;font-size:15px;color:var(--blue);transform:translateY(-50%)}
.week.current{background:var(--pill);border-radius:18px;padding:8px 10px}
.tile{position:absolute;width:166px;height:50px;background:var(--blue);border-radius:6px;color:var(--white);font-size:15px;display:flex;align-items:center;justify-content:space-between;padding:0 12px 0 14px}
.tile svg{width:26px;height:26px}
</style>
</head>
<body>
<svg width="0" height="0" style="position:absolute">
  <defs>
    <symbol id="i-home" viewBox="0 0 24 24"><path d="M12 3 2 12h3v8h5v-5h4v5h5v-8h3z" fill="currentColor"/></symbol>
    <symbol id="i-user" viewBox="0 0 24 24"><circle cx="12" cy="8" r="4" fill="currentColor"/><path d="M4 21c0-5 3.6-7 8-7s8 2 8 7z" fill="currentColor"/></symbol>
    <symbol id="i-bell" viewBox="0 0 24 24"><path d="M12 3a6 6 0 0 0-6 6v5l-2 3h16l-2-3V9a6 6 0 0 0-6-6zm-2 15a2 2 0 0 0 4 0z" fill="currentColor"/></symbol>
    <symbol id="i-loans" viewBox="0 0 24 24"><circle cx="10" cy="5" r="2.5" fill="currentColor"/><path d="M6 9h8l2 4a6 6 0 1 1-12 0z" fill="currentColor"/><circle cx="17" cy="17" r="4.5" fill="#fff" stroke="currentColor" stroke-width="1.6"/></symbol>
    <symbol id="i-doc" viewBox="0 0 24 24"><path d="M5 2h10l4 4v16H5z" fill="currentColor"/><path d="M8 10h8M8 13h8M8 16h8M8 7h5" stroke="#fff" stroke-width="1.4"/></symbol>
    <symbol id="i-report" viewBox="0 0 24 24"><path d="M5 2h10l4 4v16H5z" fill="currentColor"/><path d="M9 18v-4M12 18v-7M15 18v-5" stroke="#fff" stroke-width="1.8"/></symbol>
    <symbol id="i-gear" viewBox="0 0 24 24"><circle cx="12" cy="12" r="7" fill="none" stroke="currentColor" stroke-width="4" stroke-dasharray="3 2.5"/><circle cx="12" cy="12" r="4" fill="none" stroke="currentColor" stroke-width="2"/></symbol>
  </defs>
</svg>

<main class="stage">

  <!-- Home screen -->
  <section class="screen" style="left:94px">
    <div class="brand">LoomKit</div>
    <div class="round-icon" style="left:222px;top:37px;color:var(--green)"><svg><use href="#i-home"/></svg></div>
    <div class="round-icon" style="left:278px;top:37px;color:var(--blue)"><svg><use href="#i-user"/></svg></div>
    <div class="round-icon" style="left:334px;top:37px;color:var(--blue)"><svg><use href="#i-bell"/></svg></div>
    <div class="divider" style="left:20px;width:352px;top:111px"></div>

    <div class="stat" style="left:21px">0 Disbursed<br>$ 30,000</div>
    <div class="stat" style="left:111px">0 Collected<br>$ 20,000</div>
    <div class="stat" style="left:202px">0 Active Client<br>$ 50</div>
    <div class="stat" style="left:292px">0 New Clients<br>$ 30</div>

    <div class="section-title" style="left:21px;top:208px">Filters</div>
    <div class="chip" style="left:21px;top:242px;width:100px">Loan Officier</div>
    <div class="chip" style="left:134px;top:242px;width:71px">Branch</div>
    <div class="chip" style="left:219px;top:242px;width:58px">Fund</div>
    <div class="chip" style="left:293px;top:242px;width:80px">Product</div>

    <div class="metric-label" style="left:21px;top:311px">Near Due</div>
    <div class="metric-value" style="top:311px">$ 25, 00, 000</div>
    <div class="track" style="top:334px"><span></span></div>
    <div class="metric-label" style="left:21px;top:370px">Due</div>
    <div class="metric-value" style="top:370px">$ 34, 000</div>
    <div class="track" style="top:394px"><span></span></div>
    <div class="metric-label" style="left:21px;top:428px">Pending Disbursement</div>
    <div class="metric-value" style="top:428px">$ 30, 000</div>
    <div class="track" style="top:452px"><span></span></div>
    <div class="metric-label" style="left:21px;top:487px">Active Loan</div>
    <div class="metric-value" style="top:487px">$ 20, 000</div>
    <div class="track" style="top:511px"><span></span></div>

    <div class="divider" style="left:20px;width:352px;top:550px"></div>
    <div class="section-title" style="left:21px;top:571px">Reports</div>
    <div class="bar" style="left:29px;top:653px;width:22px;height:61px"></div>
    <div class="bar" style="left:69px;top:632px;width:22px;height:82px"></div>
    <div class="bar" style="left:111px;top:678px;width:22px;height:36px"></div>
    <div class="bar" style="left:152px;top:672px;width:22px;height:42px"></div>
    <div class="bar up" style="left:192px;top:631px;width:22px;height:83px"></div>
    <div class="bar up" style="left:235px;top:601px;width:22px;height:113px"></div>
    <div class="axis" style="left:22px;width:242px;top:714px"></div>
    <div class="tick" style="left:40px;top:718px">F1</div>
    <div class="tick" style="left:80px;top:718px">F2</div>
    <div class="tick" style="left:122px;top:718px">F3</div>
    <div class="tick" style="left:163px;top:718px">F4</div>
    <div class="tick" style="left:203px;top:718px">F5</div>
    <div class="tick" style="left:246px;top:718px">F6</div>
    <div class="btn-grad" style="left:294px;top:693px;width:78px;height:29px;font-size:14px">Next</div>

    <nav class="nav">
      <div class="nav-item active" style="left:38px"><svg><use href="#i-home"/></svg>Home</div>
      <div class="nav-item" style="left:115px"><svg><use href="#i-loans"/></svg>Loans</div>
      <div class="nav-item" style="left:193px"><svg><use href="#i-doc"/></svg>Summary</div>
      <div class="nav-item" style="left:271px"><svg><use href="#i-report"/></svg>Report</div>
      <div class="nav-item" style="left:349px"><svg><use href="#i-gear"/></svg>Settings</div>
    </nav>
  </section>

  <!-- Loan summary screen -->
  <section class="screen" style="left:574px;width:388px">
    <div class="title" style="left:17px;top:48px"><span style="color:var(--blue)">Loan</span> <span style="color:var(--green)">Summary</span></div>
    <div class="round-icon" style="left:330px;top:30px;color:var(--green)"><svg><use href="#i-doc"/></svg></div>
    <div class="divider" style="left:17px;width:353px;top:94px"></div>
    <table class="summary-table">
      <tr><td>Loan reference No 1</td><td>3213</td></tr>
      <tr><td>Loan status</td><td>Active</td></tr>
      <tr><td>Date Disbursed</td><td>13 Jul 2024</td></tr>
      <tr><td>Data Approved</td><td>20 Jul 2024</td></tr>
      <tr><td>Last repayment date</td><td>27 Jul 2024</td></tr>
      <tr><td>Next repayment date</td><td>27 Jul 2024</td></tr>
      <tr><td>Amount Disbursed</td><td>$30,000</td></tr>
      <tr><td>Amount outstanding</td><td>$30,000</td></tr>
      <tr><td>Overdue Days</td><td>30</td></tr>
    </table>
    <div class="btn-grad" style="left:138px;top:679px;width:110px;height:42px;font-size:18px">Next</div>

    <nav class="nav">
      <div class="nav-item" style="left:35px"><svg><use href="#i-home"/></svg>Home</div>
      <div class="nav-item" style="left:112px"><svg><use href="#i-loans"/></svg>Loans</div>
      <div class="nav-item active blue" style="left:190px"><svg><use href="#i-doc"/></svg>Summary</div>
      <div class="nav-item" style="left:268px"><svg><use href="#i-report"/></svg>Report</div>
      <div class="nav-item" style="left:346px"><svg><use href="#i-gear"/></svg>Settings</div>
    </nav>
  </section>

  <!-- Report screen -->
  <section class="screen" style="left:1056px;width:388px">
    <div class="title" style="left:16px;top:46px;color:var(--blue)">Report</div>
    <div class="round-icon" style="left:329px;top:30px;color:var(--green)"><svg><use href="#i-report"/></svg></div>
    <div class="divider" style="left:16px;width:354px;top:93px"></div>
    <div class="total">Total loan $35,00,000</div>

    <div class="chip" style="left:17px;top:178px;width:100px;height:34px">Loan Officier</div>
    <div class="chip" style="left:130px;top:178px;width:71px;height:34px">Branch</div>
    <div class="chip" style="left:214px;top:178px;width:60px;height:34px">Fund</div>
    <div class="chip" style="left:289px;top:178px;width:80px;height:34px">Product</div>

    <div class="btn-grad toggle" style="left:80px;width:110px">Profit</div>
    <div class="toggle off" style="left:214px;width:90px">Loss</div>

    <div class="week" style="left:17px">Week 1</div>
    <div class="week" style="left:117px">Week 2</div>
    <div class="week current" style="left:207px">Week 3</div>
    <div class="week" style="left:317px">Week 4</div>

    <div class="bar" style="left:36px;top:474px;width:31px;height:84px"></div>
    <div class="bar" style="left:90px;top:445px;width:31px;height:113px"></div>
    <div class="bar" style="left:148px;top:508px;width:31px;height:50px"></div>
    <div class="bar up" style="left:205px;top:379px;width:30px;height:179px"></div>
    <div class="bar" style="left:260px;top:500px;width:30px;height:58px"></div>
    <div class="bar" style="left:320px;top:482px;width:29px;height:76px"></div>
    <div class="axis" style="left:25px;width:335px;top:558px"></div>
    <div class="tick" style="left:52px;top:564px">Jan</div>
    <div class="tick" style="left:106px;top:564px">Feb</div>
    <div class="tick" style="left:168px;top:564px">Mar</div>
    <div class="tick" style="left:222px;top:564px">April</div>
    <div class="tick" style="left:275px;top:564px">May</div>
    <div class="tick" style="left:334px;top:564px">June</div>

    <div class="tile" style="left:17px;top:604px">Revenue $300
      <svg viewBox="0 0 24 24" fill="none" stroke="#fff" stroke-width="1.8"><circle cx="12" cy="7" r="4"/><path d="M3 12v6l4 3h10l4-3v-6"/></svg></div>
    <div class="tile" style="left:194px;top:604px">Expenses $350
      <svg viewBox="0 0 24 24" fill="#fff"><rect x="3" y="9" width="16" height="11" rx="2"/><path d="M8 8 16 3l2 4z"/></svg></div>
    <div class="tile" style="left:17px;top:672px">Tax $200
      <svg viewBox="0 0 24 24" fill="#fff"><rect x="9" y="2" width="12" height="18" rx="1"/><circle cx="8" cy="15" r="6" stroke="var(--blue)" stroke-width="1.5"/></svg></div>
    <div class="tile" style="left:194px;top:672px">Salaries $3500
      <svg viewBox="0 0 24 24" fill="none" stroke="#fff" stroke-width="1.8"><rect x="3" y="8" width="18" height="13" rx="1"/><path d="M3 8l9 7 9-7M7 8V3h10v5"/></svg></div>

    <nav class="nav">
      <div class="nav-item" style="left:35px"><svg><use href="#i-home"/></svg>Home</div>
      <div class="nav-item" style="left:111px"><svg><use href="#i-loans"/></svg>Loans</div>
      <div class="nav-item" style="left:189px"><svg><use href="#i-doc"/></svg>Summary</div>
      <div class="nav-item active" style="left:267px"><svg><use href="#i-report"/></svg>Report</div>
      <div class="nav-item" style="left:345px"><svg><use href="#i-gear"/></svg>Settings</div>
    </nav>
  </section>

</main>
</body>
</html>
```